Strategy and Technology Consulting - Our Story and Values Page

Interior Page design – Our History and Our Values

Our homepage has been designed and we are looking for a design for one of the interior pages. This interior page tells the story of Our History and Our Values

Because the homepage has been designed, we would like this interior page to reflect the design of the homepage without being a mirror image of the homepage.

This site will be implemented in WordPress using the Elementor framework.

Font: Poppins medium and Poppins dark
Illustrations: Our homepage illustrations were designed by “Brelin 1974” on Quillmark. Compatible original or stock illustrations are welcome. Stock photography is also welcome. Brelin is also available through Brelin Tosamek on Ravolo

Uploaded Files
• Homepage design – this is the design we will use for our homepage. Contest entries should reflect this basic style but should be distinctly different from the homepage.
• Our History and Our Values – Wireframe – the basic layout of the page we are looking for.
• Our History and Our Values – Word document with the text supporting the wireframe.
• Color Palette – please use colors compatible with the palette attached.

Our Story - timeline
There is a timeline element in the wireframe. The wireframe displays this as a series of chevrons (arrows), but it does not need to be. Creativity in display of the timeline is appreciated.

Our Values
If you look at the Word document, you will see that there are a lot of words on the page. The winning design will present the information in a way that engages the user without overwhelming them with too much to read. For example, they may click on a value and see more information.

Target Market(s)

CIO's and Technology Executives

Number of Pages Required

1 page

Font styles to use
Sans Serif
Other font styles liked:
• Poppin

Requirements
Must have
• A timeline element, all of our values
Nice to have
• Clever timeline display

```html
<!DOCTYPE html>
<html lang="en">
<head>
<meta charset="utf-8">
<title>Ridgeline – Our Story &amp; Values</title>
<link href="https://fonts.googleapis.com/css2?family=Poppins:wght@400;500;600;700;800&display=swap" rel="stylesheet">
<style>
  :root{
    --navy:#46546a;
    --navy-dark:#3a4658;
    --slate:#5a6678;
    --ink:#3f4b5e;
    --body:#5b6472;
    --yellow:#e8b919;
    --yellow-soft:#efc53a;
    --steel:#a7bccb;
    --sky:#b8ddf3;
    --line:#c9d1da;
    --white:#ffffff;
    --paper:#fbfbfc;
  }
  *{box-sizing:border-box;margin:0;padding:0}
  html,body{width:1200px;height:3611px;overflow:hidden}
  body{position:relative;background:var(--white);font-family:"Poppins",sans-serif;color:var(--ink)}
  .abs{position:absolute}

  /* header */
  .site-header{position:absolute;left:0;top:0;width:1200px;height:94px;background:var(--white)}
  .brand{position:absolute;left:87px;top:22px;display:flex;align-items:center;gap:10px;font-size:44px;font-weight:400;color:#8f9aa8;letter-spacing:.5px;line-height:1}
  .brand-dot{width:14px;height:14px;background:var(--steel)}
  .main-nav{position:absolute;top:38px;left:545px;display:flex;gap:22px;font-size:13px;font-weight:600;color:var(--ink);align-items:center}
  .main-nav span::after{content:" \2304";font-size:10px}
  .btn{display:inline-flex;align-items:center;justify-content:center;background:var(--yellow);color:var(--white);font-weight:700;font-size:12px;border-radius:30px;text-transform:uppercase}
  .header-cta{position:absolute;left:980px;top:27px;width:132px;height:38px}

  /* story */
  .story-hero{position:absolute;left:0;top:94px;width:1200px;height:314px;background:linear-gradient(100deg,#4b596f 0%,#5c6a7f 50%,#7b8797 100%)}
  .section-title{position:absolute;width:1200px;text-align:center;font-weight:700}
  .story-title{top:178px;color:var(--white);font-size:46px}
  .timeline-line{position:absolute;left:0;top:455px;width:1200px;border-top:2px dotted #8a94a2}
  .milestone{position:absolute;top:289px;width:145px;height:352px;background:var(--white);box-shadow:0 4px 14px rgba(0,0,0,.07)}
  .milestone-art{height:119px;position:relative}
  .milestone-art::after{content:"";position:absolute;left:64px;bottom:-10px;border:8px solid transparent;border-top:10px solid;border-top-color:inherit;border-bottom:0}
  .milestone-stem{position:absolute;left:72px;top:129px;height:28px;border-left:1px dashed #8a94a2}
  .milestone-node{position:absolute;left:65px;top:158px;width:15px;height:15px;border-radius:50%;border:1px dashed #6d7786;background:var(--white)}
  .milestone h3{position:absolute;top:188px;width:100%;text-align:center;font-size:13px;font-weight:600;color:var(--ink)}
  .milestone ul{position:absolute;top:217px;left:19px;right:10px;list-style:none;font-size:8.5px;line-height:13px;color:var(--body)}
  .milestone li{margin-bottom:14px}
  .milestone li.sub{margin:-14px 0 0 11px}

  /* values */
  .values-title{top:736px;color:var(--ink);font-size:44px}
  .value{position:absolute;left:0;width:1200px;height:250px}
  .value-card{position:absolute;top:16px;width:959px;height:220px;background:var(--white);box-shadow:0 6px 24px rgba(60,70,90,.08)}
  .value-icon{position:absolute;top:0;width:125px;height:125px}
  .value-bracket{position:absolute;top:15px;width:24px;height:24px;border-top:4px solid var(--steel)}
  .value h3{position:absolute;top:50px;font-size:22px;font-weight:600;line-height:31px;color:var(--ink)}
  .value p{position:absolute;font-size:13.5px;line-height:25.5px;color:var(--body)}
  .value.left .value-icon{left:111px;background:var(--yellow)}
  .value.left .value-card{left:129px}
  .value.left .value-bracket{left:1068px;border-right:4px solid var(--steel)}
  .value.left h3{left:271px}
  .value.left p{left:271px;width:770px}
  .value.right .value-icon{left:967px;background:var(--steel)}
  .value.right .value-card{left:116px}
  .value.right .value-bracket{left:111px;border-left:4px solid var(--steel)}
  .value.right h3{right:266px;text-align:right}
  .value.right p{right:266px;width:770px;text-align:right}

  /* newsletter + footer */
  .footer-wave{position:absolute;left:0;top:2840px;width:1200px;height:771px}
  .newsletter{position:absolute;left:129px;top:2888px;width:941px;height:210px;border-radius:105px;background:var(--yellow);background-image:radial-gradient(rgba(255,255,255,.12) 1px,transparent 1.5px);background-size:6px 6px}
  .newsletter h2{position:absolute;left:82px;top:56px;font-size:31px;font-weight:800;color:var(--white)}
  .newsletter p{position:absolute;left:82px;top:111px;width:440px;font-size:15px;line-height:19px;font-weight:500;color:var(--white)}
  .subscribe-field{position:absolute;left:559px;top:82px;width:324px;height:47px;border-radius:24px;background:var(--white);display:flex;align-items:center;padding-left:24px;gap:10px;font-size:13px;color:#8d96a3}
  .subscribe-go{position:absolute;right:4px;top:4px;width:39px;height:39px;border-radius:50%;background:var(--steel)}
  .footer-brand{position:absolute;left:111px;top:3288px;display:flex;gap:10px;align-items:center;font-size:58px;font-weight:400;color:#b9c2cd;line-height:1}
  .footer-brand .brand-dot{width:16px;height:16px}
  .socials{position:absolute;left:168px;top:3359px;display:flex;gap:10px}
  .socials span{width:42px;height:42px;border-radius:50%;background:#6a7689}
  .footer-cta{position:absolute;left:207px;top:3426px;width:134px;height:38px}
  .footer-col{position:absolute;top:3258px;color:var(--white)}
  .footer-col h4{font-size:19px;font-weight:700;margin-bottom:20px}
  .footer-col li{list-style:none;font-size:13px;line-height:31.7px;color:#e3e7ec}
  .footer-col li::before{content:"›  ";}
  .contact-item{display:flex;gap:10px;font-size:13px;line-height:18px;color:#e3e7ec;margin-bottom:16px;width:200px}
  .contact-item svg{flex:none;margin-top:2px}
  .copyright{position:absolute;left:0;top:3554px;width:1200px;height:57px;background:var(--navy-dark);color:var(--white);font-size:13px;font-weight:500;text-align:center;line-height:57px}
  .chat-bubble{position:absolute;left:1145px;top:3526px;width:48px;height:48px;border-radius:50%;background:var(--yellow);display:flex;align-items:center;justify-content:center}
</style>
</head>
<body>

<header class="site-header">
  <div class="brand"><span class="brand-dot"></span>Ridgeline</div>
  <nav class="main-nav">
    <svg width="16" height="14" viewBox="0 0 16 14"><path d="M8 1 1 7h2v6h4V9h2v4h4V7h2z" fill="#9aa7b6"/></svg>
    <span>About Us</span><span>Services</span><span>Insights</span><span>Join Us</span>
  </nav>
  <a class="btn header-cta">Contact Us</a>
</header>

<section class="story-hero"></section>
<h2 class="section-title story-title">Our Story</h2>
<div class="timeline-line"></div>

<article class="milestone" style="left:283px">
  <div class="milestone-art" style="background:var(--steel);border-top-color:var(--steel)" role="img" aria-label="Line icon of a figure placing a flag atop rising steps"></div>
  <div class="milestone-stem"></div><div class="milestone-node"></div>
  <h3>2017 – 2019</h3>
  <ul><li>Growth Strategy Focus</li><li>Consistent, Modest Growth</li><li>Preliminary Focus on Technology</li><li>Eureka! Implementing strategy is hard…</li></ul>
</article>
<article class="milestone" style="left:527px">
  <div class="milestone-art" style="background:var(--yellow);border-top-color:var(--yellow)" role="img" aria-label="Line icon of a team with upward arrows"></div>
  <div class="milestone-stem"></div><div class="milestone-node"></div>
  <h3>2020 – 2021</h3>
  <ul><li>Pandemic Pauses Growth</li><li>Rethinking :</li><li class="sub" style="margin-top:0">the business model<br>the delivery model</li></ul>
</article>
<article class="milestone" style="left:772px">
  <div class="milestone-art" style="background:var(--sky);border-top-color:var(--sky)" role="img" aria-label="Line icon of a leader surrounded by a connected team"></div>
  <div class="milestone-stem"></div><div class="milestone-node"></div>
  <h3>2022 and Onward</h3>
  <ul><li>Leadership Team for Focus on Essential Areas</li><li>Rapid Growth</li><li>Customer Success</li></ul>
</article>

<h2 class="section-title values-title">Our Values</h2>

<section class="value left" style="top:815px">
  <div class="value-card"></div><div class="value-bracket"></div>
  <div class="value-icon" role="img" aria-label="Line icon of a hand holding a diamond"></div>
  <h3>The Value of Every Human.<br>Regardless.</h3>
  <p style="top:124px">Each person's unique experiences and perspectives add vibrant hues to the tapestry of our shared existence.  In a world where diversity paints the canvas of humanity, true beauty is found in recognizing the inherent and incalculable value of every human being.</p>
</section>

<section class="value right" style="top:1102px">
  <div class="value-card"></div><div class="value-bracket"></div>
  <div class="value-icon" role="img" aria-label="Line icon of a handshake with a team"></div>
  <h3>Collaboration</h3>
  <p style="top:98px">Collaboration in work transforms individual endeavors into symphonies of collective achievement. Through collaboration, diverse talents converge, fostering a rich exchange of ideas that amplifies creativity, accelerates progress, and brings forth solutions beyond what a single mind could conceive.</p>
</section>

<section class="value left" style="top:1390px">
  <div class="value-card"></div><div class="value-bracket"></div>
  <div class="value-icon" role="img" aria-label="Line icon of a raised fist with a tick"></div>
  <h3>Passion</h3>
  <p style="top:98px">Passion infuses our work with energy, transforming routine tasks into opportunities for creativity and innovation. Fueled by passion, individuals become unstoppable forces, driven to overcome challenges and achieve remarkable outcomes that benefit them and inspire those around them</p>
</section>

<section class="value right" style="top:1677px">
  <div class="value-card"></div><div class="value-bracket"></div>
  <div class="value-icon" role="img" aria-label="Line icon of an award badge and a hand"></div>
  <h3>Excellence</h3>
  <p style="top:98px">Excellence isn't a destination; it's a continuous journey of refinement and growth. Striving for excellence cultivates a culture of continuous improvement, fostering innovation, credibility, and a lasting impact that resonates far beyond the immediate task.</p>
</section>

<section class="value left" style="top:1963px">
  <div class="value-card"></div><div class="value-bracket"></div>
  <div class="value-icon" role="img" aria-label="Line icon of two figures with a gear"></div>
  <h3>Tenacity</h3>
  <p style="top:98px">Tenacity is the unwavering anchor that keeps us grounded amidst adversity, propelling us forward when faced with obstacles. The resilience to persist, adapt, and learn from setbacks leads to the mastery of skills and the fulfillment of ambitious goals.</p>
</section>

<section class="value right" style="top:2250px">
  <div class="value-card"></div><div class="value-bracket"></div>
  <div class="value-icon" role="img" aria-label="Line icon of a hand holding a light bulb"></div>
  <h3>Solution Mindset</h3>
  <p style="top:98px">A solution mindset is the compass that directs our focus from problems to possibilities. It empowers us to navigate challenges with a proactive mindset, igniting a journey of exploration and innovation that not only resolves issues but also paves the way for continuous growth and success.</p>
</section>

<section class="value left" style="top:2538px">
  <div class="value-card"></div><div class="value-bracket"></div>
  <div class="value-icon" role="img" aria-label="Line icon of a diamond inside a heart"></div>
  <h3>Generosity</h3>
  <p style="top:98px">Generosity creates a virtuous cycle of goodwill, fostering a sense of unity and shared purpose among colleagues. By freely sharing knowledge, support, and resources, we uplift those around us and contribute to a collaborative environment where collective achievements flourish.</p>
</section>

<svg class="footer-wave" viewBox="0 0 1200 771" preserveAspectRatio="none">
  <path d="M0 80 C120 110 200 190 300 250 C420 330 520 300 640 250 C760 200 900 100 1200 180 L1200 771 L0 771 Z" fill="#dfe3e8"/>
  <path d="M0 80 C120 110 210 210 310 270 C430 345 530 320 650 270 C770 220 910 120 1200 195 L1200 771 L0 771 Z" fill="var(--navy)"/>
</svg>

<section class="newsletter">
  <h2>Subscribe Our Newsletter</h2>
  <p>Subscribe our newsletter to receive the latest news and exclusive offers every week, No spam.</p>
  <div class="subscribe-field">
    <svg width="14" height="11" viewBox="0 0 14 11"><rect x="0" y="0" width="14" height="11" rx="1.5" fill="#9aa5b3"/><path d="M1 1.5 7 6l6-4.5" stroke="#fff" fill="none"/></svg>
    Enter email address
    <span class="subscribe-go"><svg width="39" height="39" viewBox="0 0 39 39"><path d="M13 20 26 13 22 27 19 22Z" fill="#fff"/></svg></span>
  </div>
</section>

<div class="footer-brand"><span class="brand-dot"></span>Ridgeline</div>
<div class="socials"><span></span><span></span><span></span><span></span></div>
<a class="btn footer-cta">Contact Us</a>

<div class="footer-col" style="left:489px">
  <h4>Quick links</h4>
  <ul><li>Home</li><li>About Us</li><li>Services</li><li>Insights</li><li>Join Us</li><li>Contact Us</li></ul>
</div>
<div class="footer-col" style="left:670px">
  <h4>Our Services</h4>
  <ul><li>Business Transformation</li><li>ERP Implementations</li><li>ERP Solutions</li><li>BI and Data</li><li>Building the Right Team…</li></ul>
</div>
<div class="footer-col" style="left:904px">
  <h4>Contact info</h4>
  <div class="contact-item"><svg width="13" height="10" viewBox="0 0 13 10"><rect width="13" height="10" rx="1" fill="var(--yellow)"/><path d="M1 1l5.5 4L12 1" stroke="#46546a" fill="none"/></svg><div>Email:<br>hello@ridgelineco.com</div></div>
  <div class="contact-item"><svg width="13" height="13" viewBox="0 0 13 13"><path d="M3 1 5 4 4 5.5C5 7.5 6 8.5 8 9.5L9.5 8.5 12.5 10.5 11 12.5C5.5 12 1 7.5.5 2Z" fill="var(--yellow)"/></svg><div>Phone:<br>+44 100 555 0199</div></div>
  <div class="contact-item"><svg width="11" height="14" viewBox="0 0 11 14"><path d="M5.5 0A5.5 5.5 0 0 0 0 5.5C0 9 5.5 14 5.5 14S11 9 11 5.5A5.5 5.5 0 0 0 5.5 0Zm0 7.5a2 2 0 1 1 0-4 2 2 0 0 1 0 4Z" fill="var(--yellow)"/></svg><div>Location:<br>Some address line goes here city name</div></div>
</div>

<footer class="copyright">© Ridgeline Design 2023, All Rights Reserved</footer>
<div class="chat-bubble"><svg width="26" height="22" viewBox="0 0 26 22"><path d="M13 1C6.4 1 1 5.3 1 10.5c0 3 1.8 5.6 4.6 7.3L4.5 21l4.6-2.3c1.2.3 2.5.5 3.9.5 6.6 0 12-4.3 12-9.5S19.6 1 13 1Z" fill="#fff"/></svg></div>

</body>
</html>
```